Design a website for our small self storage business

We're looking for a freelance web designer who can produce a good-looking design for our small business website (no coding necessary). We will provide a list of pages to design, along with content outlines.

Key skills:
- Graphic design
- Responsive web design
- Proficiency with a modern web design tool such as Figma, Adobe Xd, or InVision

Please send relevant previous work (preferably in an inspectable format such as Figma or Invision).

```html
<!DOCTYPE html>
<html lang="en">
<head>
<meta charset="utf-8">
<title>Marlow Self Storage Westbrook</title>
<link href="https://fonts.googleapis.com/css2?family=Poppins:wght@400;500;600;700;800&family=Roboto:wght@400;500&display=swap" rel="stylesheet">
<style>
:root{
  --navy:#0d4a8c;
  --red:#e31e24;
  --ink:#333;
  --muted:#555;
  --grey:#efefef;
  --row:#e9eff6;
  --white:#fff;
}
*{box-sizing:border-box;margin:0;padding:0}
html,body{width:1200px;height:3937px;overflow:hidden;background:var(--white)}
body{font-family:'Poppins',sans-serif;color:var(--ink);position:relative}
.abs{position:absolute}
a{color:inherit;text-decoration:none}

/* header */
.header{left:0;top:0;width:1200px;height:133px;background:var(--white)}
.brand{left:75px;top:22px;width:170px;text-align:center;color:var(--navy);font-weight:600;line-height:1}
.brand .mark{display:block;width:26px;height:26px;background:var(--navy);margin:0 auto 6px}
.brand .name{font-size:30px;letter-spacing:0.5px}
.brand .sub{font-size:15px;letter-spacing:1px;margin-top:3px}
.nav{top:58px;left:404px;font-size:16px;font-weight:500;color:#222;display:flex}
.nav a{margin-right:44px}
.nav a.active{color:var(--red)}
.call-icon{left:858px;top:46px;width:44px;height:44px;border-radius:50%;background:var(--navy)}
.call{left:911px;top:40px;line-height:1}
.call .lbl{font-size:16px;font-weight:600;color:#222}
.call .num{font-size:27px;font-weight:700;color:var(--red);margin-top:6px}

/* hero */
.hero{left:0;top:133px;width:1200px;height:687px;background:linear-gradient(100deg,#8d8f93 0%,#4b5a70 35%,#3d4350 60%,#2e3a55 100%)}
.hero-panel{left:569px;top:281px;width:631px;height:389px;background:rgba(40,40,40,.55)}
.hero-text{right:73px;top:318px;width:640px;text-align:right;color:var(--white)}
.hero-text h1{font-size:44px;line-height:60px;font-weight:500;white-space:nowrap}
.hero-text h1 b{font-weight:700}
.hero-text p{font-size:17px;line-height:29px;margin:12px 0 0 auto;width:530px}
.btn{display:block;background:var(--red);color:var(--white);font-weight:700;text-align:center;text-transform:uppercase}
.hero-btn{display:inline-block;margin-top:22px;width:217px;height:56px;line-height:56px;font-size:20px}

/* section headings */
.sec-title{left:0;width:1200px;text-align:center;color:var(--navy);font-weight:700;font-size:37px;display:flex;justify-content:center;align-items:center}
.sec-title::before,.sec-title::after{content:"";width:88px;height:2px;background:var(--navy);margin:0 22px}

/* units */
.units{left:0;top:820px;width:1200px;height:675px;background:var(--grey)}
.units-note{left:0;top:954px;width:1200px;text-align:center;font-family:'Roboto',sans-serif;font-size:15px;line-height:28px;color:var(--muted)}
.table{left:75px;top:1030px;width:1052px;border-collapse:collapse;font-family:'Roboto',sans-serif;font-size:15px}
.table th{background:var(--navy);color:var(--white);font-weight:400;text-align:left;height:62px;padding-left:21px;border-right:3px solid var(--grey)}
.table th:last-child{border-right:0}
.table td{height:64.5px;padding-left:21px;color:#444;background:var(--white)}
.table tr:nth-child(odd) td{background:var(--row)}
.table .reserve{color:var(--red);font-weight:500;text-decoration:underline}
.load-btn{left:521px;top:1373px;width:161px;height:45px;line-height:45px;font-size:15px}

/* advantages */
.card{top:1653px;width:328px;height:313px;background:var(--white);border-radius:6px;box-shadow:0 2px 12px rgba(0,0,0,.18);text-align:center}
.card.featured{border:3px solid var(--red)}
.card .icon{width:119px;height:119px;border-radius:50%;margin:24px auto 0;background:linear-gradient(180deg,var(--red) 0%,#7a2a5c 50%,var(--navy) 100%);display:flex;align-items:center;justify-content:center}
.card h3{margin-top:22px;color:var(--navy);font-size:24px;font-weight:600;letter-spacing:.5px}
.card p{margin:10px auto 0;width:270px;font-size:15.5px;line-height:28px;color:var(--muted)}

/* feature rows */
.band-grey{left:0;top:2037px;width:1200px;height:694px;background:var(--grey)}
.feat-title{text-align:center;color:var(--navy);font-weight:700;font-size:38px;line-height:49px}
.feat-title .rule{display:inline-flex;align-items:center}
.feat-title .rule::before,.feat-title .rule::after{content:"";width:88px;height:2px;background:var(--navy);margin:0 14px}
.feat-text{text-align:center;font-size:17.5px;line-height:30.5px;color:#444}
.feat-btn{width:207px;height:57px;line-height:57px;font-size:19px}
.red-block{background:var(--red)}
.photo{border:5px solid var(--white);box-shadow:0 3px 10px rgba(0,0,0,.25)}

/* footer */
.footer{left:0;top:3422px;width:1200px;height:453px;background:#ededed}
.foot-brand{left:76px;top:3545px;width:207px;text-align:center;color:var(--navy);font-weight:600;line-height:1}
.foot-brand .mark{display:block;width:34px;height:34px;background:var(--navy);margin:0 auto 8px}
.foot-brand .name{font-size:40px}
.foot-brand .sub{font-size:19px;letter-spacing:1px;margin-top:4px}
.foot-links{left:336px;top:3509px;font-size:16px;line-height:38.5px;color:#333}
.contact{left:521px;top:3509px;font-size:15.5px;color:#333}
.contact h4{font-size:18px;font-weight:600;margin-bottom:10px}
.contact .row{display:flex;line-height:28px;margin-bottom:5px}
.contact .row svg{flex:none;margin:7px 14px 0 0}
.contact .open{font-weight:600;font-size:17px;margin-top:10px}
.contact .hours{color:var(--navy);font-weight:600;font-size:16px;margin-top:4px}
.map{left:824px;top:3515px;width:303px;height:320px;background:linear-gradient(135deg,#eef0f3,#dfe4ea);border:5px solid var(--white);box-shadow:0 2px 8px rgba(0,0,0,.2)}
.copyright{left:0;top:3875px;width:1200px;height:62px;background:var(--navy);color:var(--white);font-size:14px;text-align:center;line-height:62px}
</style>
</head>
<body>

<header class="header abs">
  <div class="brand abs"><span class="mark"></span><div class="name">MARLOW</div><div class="sub">SELF STORAGE</div></div>
  <nav class="nav abs"><a class="active" href="#">HOME</a><a href="#">UNITS</a><a href="#">PAY ONLINE</a><a href="#">CONTACT US</a></nav>
  <div class="call-icon abs">
    <svg width="44" height="44" viewBox="0 0 44 44"><path d="M17 14c1-1 2-1 3 0l2 3c.5 1 .3 2-.5 2.5l-1 .8c.8 2 2.2 3.4 4.2 4.2l.8-1c.5-.8 1.5-1 2.5-.5l3 2c1 1 1 2 0 3-2 2-5 2-8-1s-7-7-7-10c0-1 .3-2 1-3z" fill="#fff"/></svg>
  </div>
  <div class="call abs"><div class="lbl">CALL US:</div><div class="num">1-800-555-0142</div></div>
</header>

<section class="hero abs" role="img" aria-label="Photo of an open self storage unit with a bicycle, mattress and moving boxes in a corridor of blue roll-up doors"></section>
<div class="hero-panel abs"></div>
<div class="hero-text abs">
  <h1><b>WELCOME TO MARLOW</b><br>SELF STORAGE WESTBROOK</h1>
  <p>Marlow Self Storage Westbrook Located on Marlow St. between Birch Ave. and Linden Ave. near Westbrook Civic Center in Cedar Valley.</p>
  <a class="btn hero-btn" href="#">See Our Units</a>
</div>

<section class="units abs"></section>
<h2 class="sec-title abs" style="top:885px">UNITS</h2>
<p class="units-note abs">Availability And Pricing Are Subject To Change, Please Contact Us For Current Information On<br>Availability And Current Price.</p>
<table class="table abs">
  <thead><tr><th style="width:105px">Unit Size</th><th style="width:106px">Name</th><th style="width:297px">Description</th><th style="width:142px">Location</th><th style="width:105px">Price</th><th style="width:140px">Available Units</th><th>Unit Size</th></tr></thead>
  <tbody>
    <tr><td>10 X 10</td><td>Name 1</td><td>Lorem ipsum dolor sit amet, consect</td><td>Ground floor</td><td>$20.00</td><td>2</td><td><a class="reserve" href="#">Reserve Now</a></td></tr>
    <tr><td>10 X 14</td><td>Name 1</td><td>Lorem ipsum dolor sit amet, consect</td><td>Exterior</td><td>$20.00</td><td>Sold Out</td><td><a class="reserve" href="#">Reserve Now</a></td></tr>
    <tr><td>10 X 15</td><td>Name 1</td><td>Lorem ipsum dolor sit amet, consect</td><td>"Exterior</td><td>$20.00</td><td>2</td><td><a class="reserve" href="#">Reserve Now</a></td></tr>
    <tr><td>10 X 20</td><td>Name 1</td><td>Lorem ipsum dolor sit amet, consect</td><td>Ground floor</td><td>$20.00</td><td>Sold Out</td><td><a class="reserve" href="#">Reserve Now</a></td></tr>
  </tbody>
</table>
<a class="btn load-btn abs" href="#">Load More &#9654;</a>

<h2 class="sec-title abs" style="top:1549px">KEY ADVANTAGES</h2>
<div class="card featured abs" style="left:75px">
  <div class="icon"><svg width="56" height="56" viewBox="0 0 56 56" fill="none" stroke="#fff" stroke-width="2.5"><rect x="14" y="8" width="28" height="38" rx="2"/><path d="M20 18h16M20 25h16M20 32h10"/><circle cx="40" cy="42" r="7"/></svg></div>
  <h3>AFFORDABLE</h3>
  <p>Sed ut perspiciatis unde omnis iste natus error sit voluptatem accu santium doloremque.</p>
</div>
<div class="card abs" style="left:437px">
  <div class="icon"><svg width="56" height="56" viewBox="0 0 56 56" fill="none" stroke="#fff" stroke-width="2.5"><path d="M19 24v-6a9 9 0 0 1 18 0v6"/><rect x="13" y="24" width="30" height="22" rx="3"/><circle cx="28" cy="34" r="3"/><path d="M28 37v4"/></svg></div>
  <h3>SECURE</h3>
  <p>Sed ut perspiciatis unde omnis iste natus error sit voluptatem accu santium doloremque.</p>
</div>
<div class="card abs" style="left:798px">
  <div class="icon"><svg width="56" height="56" viewBox="0 0 56 56" fill="none" stroke="#fff" stroke-width="2.5"><circle cx="30" cy="20" r="9"/><path d="M8 40h10l8 4h14l8-8"/><path d="M18 40c4-4 10-4 14-2"/></svg></div>
  <h3>CONVENIENT</h3>
  <p>Sed ut perspiciatis unde omnis iste natus error sit voluptatem accu santium doloremque.</p>
</div>

<section class="band-grey abs"></section>
<h2 class="feat-title abs" style="left:60px;top:2186px;width:630px"><span class="rule">JUST SHOW UP WITH</span><br>YOUR STUFF</h2>
<p class="feat-text abs" style="left:80px;top:2317px;width:590px">Sed ut perspiciatis unde omnis iste natus error sit voluptatem accusantium doloremque laudantium, totam rem aperiam, eaque ipsa quae ab illo inventore veritatis et quasi architecto beatae vitae dicta sunt explicabo. Nemo enim ipsam voluptatem quia voluptas sit aspernatur aut odit aut fugit, sed quia consequuntur magni dolores.</p>
<a class="btn feat-btn abs" style="left:274px;top:2512px" href="#">Read More</a>
<div class="red-block abs" style="left:765px;top:2110px;width:362px;height:344px"></div>
<div class="photo abs" style="left:705px;top:2127px;width:391px;height:515px;background:linear-gradient(160deg,#c98a4a 0%,#d9603a 45%,#8c5a3a 100%)" role="img" aria-label="Photo of a hand taking an orange folder from a shelf"></div>

<h2 class="feat-title abs" style="left:516px;top:2880px;width:610px"><span class="rule">WHAT SHOULD I</span><br>BRING TO RENT A SPACE?</h2>
<p class="feat-text abs" style="left:526px;top:2994px;width:590px">Sed ut perspiciatis unde omnis iste natus error sit voluptatem accusantium doloremque laudantium, totam rem aperiam, eaque ipsa quae ab illo inventore veritatis et quasi architecto beatae vitae dicta sunt explicabo. Nemo enim ipsam voluptatem quia voluptas sit aspernatur aut odit aut fugit, sed quia consequuntur magni dolores.</p>
<a class="btn feat-btn abs" style="left:717px;top:3205px" href="#">Read More</a>
<div class="red-block abs" style="left:75px;top:2801px;width:361px;height:346px"></div>
<div class="photo abs" style="left:105px;top:2836px;width:392px;height:514px;background:linear-gradient(90deg,#b8262a 0%,#d23a36 40%,#9b9b96 55%,#c73532 70%,#a32a2a 100%)" role="img" aria-label="Photo of an indoor corridor lined with red storage unit doors"></div>

<footer class="footer abs"></footer>
<div class="foot-brand abs"><span class="mark"></span><div class="name">MARLOW</div><div class="sub">SELF STORAGE</div></div>
<nav class="foot-links abs"><a href="#">Home</a><br><a href="#">Units</a><br><a href="#">Pay Online</a><br><a href="#">Contact Us</a></nav>
<div class="contact abs">
  <h4>Marlow Self Storage</h4>
  <div class="row"><svg width="18" height="14" viewBox="0 0 18 14"><path d="M1 2l5-2 6 2 5-2v12l-5 2-6-2-5 2z" fill="#333"/></svg><span>4820 Marlow Street Westbrook,<br>CA 90000</span></div>
  <div class="row"><svg width="18" height="14" viewBox="0 0 18 14"><path d="M3 1c1-1 2-1 3 0l1 2c.4.7 0 1.4-.5 1.8l-.6.5c.6 1.4 1.6 2.4 3 3l.5-.6c.4-.5 1.1-.9 1.8-.5" fill="none" stroke="#333" stroke-width="2"/></svg><span>1-800-555-0142</span></div>
  <div class="row"><svg width="18" height="14" viewBox="0 0 18 14"><rect x="3" y="4" width="12" height="9" fill="#333"/><rect x="5" y="0" width="8" height="4" fill="#333"/></svg><span>1-800-555-0142</span></div>
  <div class="row"><svg width="18" height="14" viewBox="0 0 18 14"><rect x="1" y="1" width="16" height="12" fill="#333"/><path d="M1 1l8 6 8-6" stroke="#fff" stroke-width="1.5" fill="none"/></svg><span>info@companyname.com</span></div>
  <div class="open">OPEN 7 DAYS A WEEK</div>
  <div class="hours">9:30 am - 5:30 pm</div>
</div>
<div class="map abs" role="img" aria-label="Street map showing the storage facility location"></div>
<div class="copyright abs">© Copyright 2022 CompanyName All Rights Reserved</div>

</body>
</html>
```